Cybersecurity Company Profile Word Template

We are looking for designs to develop a modern, innovative, and Company Profile template. This template will be a Word template that we will convert to PDF and send to potential clients and partners. The ideal structure of the template can be found below. We would like to see designs that relate to cybersecurity and include our company colors white, black, and red (#A80402). We have attached the logo we plan to use as we are rebranding. Additionally, I have included our logo variations. Company website is https://vornelquay.io. For content placeholder text is fine. We are concerned with the overall template having the necessary sections, pages, and overall structure we have mentioned in this brief.

Ideal template flow and structure:
-Cover Page
-Company "Contact Us"
-Table of Contents
-About Company
- NAICS Codes
- 541519 - Other Computer Related Servcies
- 541512 - Computer Systems Design Services
- 541690 - Other Scientific and Technical Consulting Services
- 541511 - Custom Computer Programming Services
-CEO Statement/Message (picture/headshot will be added to this page)
-Company History
-Vision and Misson
-Team Bios- Bio will include a picrure
-Our Values
- (Short paragraph)
- Our Services
- Penetration Testing
- Red Team/Threat Emulation
- Cloud Security Assessments
- Vulnerability Management
- Managed Detection and Response
- Incident Response
- Threat Hunting
- Risk Assessments
- Simulated Phishing Campaigns
- Projects

Target Market(s)

Potential customers and partners

Industry/Entity Type

Cybersecurity

Colors

Designer to choose colors to be used in the design.

Requirements
Must have
• Red must be #a80402

```html
<!DOCTYPE html>
<html lang="en">
<head>
<meta charset="utf-8">
<title>Vornel Quay Security — Company Profile Template</title>
<link rel="stylesheet" href="https://fonts.googleapis.com/css2?family=Archivo:wdth,wght@62..125,400..900&family=Inter:wght@400;600;700&display=swap">
<style>
:root{
  --red:#a80402;
  --red-deep:#7d0302;
  --ink:#141414;
  --black:#0c0c0d;
  --paper:#f3f3f3;
  --paper-grey:#dcdcdc;
  --backdrop:#dedee0;
  --muted:#444;
}
*{box-sizing:border-box;margin:0;padding:0}
html,body{width:758px;height:1200px;overflow:hidden}
body{background:var(--backdrop);font-family:"Inter",Arial,sans-serif;color:var(--ink);position:relative}
a{color:inherit;text-decoration:none}

.cover,.spread{position:absolute;box-shadow:0 3px 8px rgba(0,0,0,.25)}
.spread{display:flex}
.page{position:relative;width:155px;height:233px;background:var(--paper);overflow:hidden}
.page.grey{background:var(--paper-grey)}
.page + .page{border-left:1px solid #c9c9c9}

.page-header{height:22px;background:linear-gradient(90deg,var(--red-deep),var(--red));color:#fff;
  font-family:"Archivo",Arial,sans-serif;font-weight:600;font-size:3.2px;letter-spacing:.2px;
  display:flex;justify-content:space-between;align-items:center;padding:0 11px 0 22px}

.photo{display:block}
.photo-red{background:radial-gradient(circle at 60% 40%,#e0262a 0%,#8a0b0d 35%,#2a0606 75%,#120303 100%)}
.photo-dark{background:radial-gradient(circle at 75% 50%,#a51215 0%,#3a0708 30%,#111 70%)}
.photo-chip{background:radial-gradient(circle at 55% 45%,#3c3c3e 0%,#241414 35%,#6a0b0d 60%,#1b0a0a 100%)}

.title{font-family:"Archivo",Arial,sans-serif;font-weight:800;font-size:13px;line-height:1.15;letter-spacing:.2px;color:var(--ink)}
.rule{height:1px;background:var(--red);margin-top:6px}
.body-text{font-size:2.5px;line-height:1.45;color:var(--muted)}
.body-text p + p{margin-top:4px}

/* Covers */
.cover{width:166px;height:234px;overflow:hidden}
.cover-front{left:212px;top:42px;background:var(--paper)}
.cover-front .hero{height:117px}
.date-tag{position:absolute;left:13px;top:12px;background:var(--red);color:#fff;font-size:5.5px;padding:4px 5px}
.brand-name{font-family:"Archivo",Arial,sans-serif;font-weight:600;color:#fff;letter-spacing:1px;display:flex;align-items:center;gap:3px}
.brand-name .mark{display:inline-block;background:var(--red)}
.cover-front .brand-name{position:absolute;right:8px;top:15px;font-size:5px}
.cover-front .brand-name .mark{width:6px;height:6px}
.cover-title{font-family:"Archivo",Arial,sans-serif;font-weight:800;font-stretch:125%;font-size:14px;line-height:1.6;text-align:center;margin-top:14px;color:var(--black)}
.cover-sub{font-family:"Archivo",Arial,sans-serif;font-weight:700;font-size:5.2px;line-height:1.75;margin:12px 0 0 18px}
.cover-foot{position:absolute;left:0;right:0;bottom:0;height:22px;background:var(--red);color:#fff;font-size:2.6px;
  display:flex;justify-content:space-around;align-items:center}
.cover-back{left:423px;top:43px;background:var(--black)}
.cover-back .hero{position:absolute;inset:0}
.cover-back .site{position:absolute;top:22px;width:100%;text-align:center;color:#ddd;font-size:5.4px}
.cover-back .brand-name{position:absolute;left:0;right:0;bottom:26px;justify-content:center;font-size:10px;letter-spacing:2px}
.cover-back .brand-name .mark{width:10px;height:10px}

/* Contact */
.contact .photo{height:113px}
.contact .block{padding:6px 15px 0 18px}
.contact-list{list-style:none;margin-top:9px;font-size:3.1px}
.contact-list li{display:flex;align-items:center;gap:8px;height:11px}
.contact-list svg{width:7px;height:7px;flex:none}

/* TOC */
.toc .block{padding:38px 16px 0 15px}
.toc-grid{display:grid;grid-template-columns:1fr 16px 1fr 10px;row-gap:7px;margin-top:11px;font-size:3px}
.toc-grid .num{font-family:"Archivo",Arial,sans-serif;font-stretch:125%;font-weight:500;font-size:4px;line-height:1}
.toc .photo{position:absolute;left:15px;right:16px;bottom:12px;height:30px}

/* About */
.about .block{padding:8px 14px 0 17px}
.about .title{font-size:12.5px}
.about .body-text{margin-top:10px}

/* NAICS */
.naics .photo{height:113px}
.naics .block{padding:16px 15px 0 17px}
.naics-codes{display:flex;gap:6px;margin-top:10px}
.naics-code{width:26px;height:29px;background:var(--red);color:#fff;padding:2px;font-size:2.3px;line-height:1.25}
.naics-code b{display:block;font-size:2.6px;font-weight:600;margin-bottom:4px}
.naics-code span{display:block;text-align:center}

/* CEO */
.ceo .block{padding:12px 10px 0 15px}
.ceo .title{font-size:12px}
.ceo-row{display:flex;gap:10px;margin-top:12px}
.ceo-card{width:28px;flex:none;text-align:center;font-size:2.6px}
.ceo-card .photo{width:27px;height:28px;margin-bottom:5px}
.ceo-card b{display:block;margin-bottom:3px}
.ceo .photo-band{position:absolute;left:15px;right:10px;bottom:15px;height:58px}

/* History */
.history{display:flex}
.history .photo{width:55px;height:211px}
.history .block{padding:12px 12px 0 18px;flex:1}
.history .body-text{margin-top:12px}

/* Vision */
.vision .block{padding:18px 12px 0 14px}
.vm-row{display:flex;gap:10px;margin-top:10px}
.vm-row .photo{width:53px;height:60px;flex:none}
.vm-col{flex:1}
.vm-head{font-family:"Archivo",Arial,sans-serif;font-weight:600;font-size:7px;display:flex;align-items:center;gap:5px;margin-bottom:6px}
.vm-head svg{width:7px;height:6px}

/* Team */
.team .block{padding:20px 14px 0 15px}
.team .title{font-size:17px}
.bio{display:flex;gap:8px;margin-top:13px}
.bio .photo{width:24px;height:26px;flex:none}
.bio-name{font-size:2.6px;font-weight:700;margin-top:3px}
.team .photo-band{position:absolute;left:0;right:0;bottom:0;height:25px}

/* Values */
.values .photo{height:113px}
.values .block{padding:16px 13px 0 17px}
.values .title{font-size:15px}
.values .body-text{margin-top:6px}

/* Services */
.services .block{padding:14px 14px 0 15px}
.services .title{font-size:15px}
.service{display:flex;margin-top:9px;height:33px}
.service-label{width:32px;flex:none;background:var(--red);color:#fff;font-family:"Archivo",Arial,sans-serif;font-weight:600;font-size:4.5px;line-height:1.25;padding:0 1px;display:flex;align-items:center;justify-content:center;text-align:center}
.service-desc{flex:1;border:1px solid var(--red);border-left:0;padding:2px 3px;font-size:2.3px;line-height:1.4;color:var(--muted)}
.services .service:first-of-type{margin-top:22px}

/* Pen test */
.pentest .block{padding:13px 9px 0 14px}
.pentest .title{font-size:10px}
.stage{color:var(--red);font-size:3.8px;font-weight:600;margin:6px 0 2px}
.step{font-size:2.5px;line-height:1.35;color:var(--muted);margin-bottom:3px}
.step b{display:block;color:var(--ink)}
.pentest .photo-band{position:absolute;left:0;right:0;bottom:0;height:26px}

/* Projects */
.projects .block{padding:24px 16px 0 14px}
.projects .title{font-size:15px}
.projects .body-text{margin-top:10px}
.projects .photo-band{position:absolute;left:0;right:0;bottom:0;height:57px}
</style>
</head>
<body>

<!-- Front cover -->
<section class="cover cover-front" aria-label="Front cover">
  <div class="photo photo-dark hero" role="img" aria-label="Glowing red padlock on a dark circuit board"></div>
  <div class="date-tag">JANUARY 2025</div>
  <div class="brand-name"><span class="mark"></span>VORNEL QUAY</div>
  <h1 class="cover-title">COVER PAGE<br>TITLE HERE</h1>
  <p class="cover-sub">COVER PAGE SUBTITLE CAN GO HERE<br>COVER PAGE SUBTITLE CAN GO HERE</p>
  <div class="cover-foot"><span>Tel: 555.014.2290</span><span>https://vornelquay.io</span><span>hello@vornelquay.io</span></div>
</section>

<!-- Back cover -->
<section class="cover cover-back" aria-label="Back cover">
  <div class="photo photo-dark hero" role="img" aria-label="Red padlock within a dark circuit pattern"></div>
  <p class="site">WWW.VORNELQUAY.IO</p>
  <div class="brand-name"><span class="mark"></span>VORNEL QUAY</div>
</section>

<!-- Spread: Contact / TOC -->
<div class="spread" style="left:68px;top:326px">
  <section class="page contact">
    <div class="page-header"><span>VORNEL QUAY SECURITY</span><span>2</span></div>
    <div class="photo photo-red" role="img" aria-label="Padlock on a red circuit board"></div>
    <div class="block">
      <h2 class="title">CONTACT US</h2>
      <div class="rule"></div>
      <ul class="contact-list">
        <li><svg viewBox="0 0 10 10" fill="none" stroke="#222" stroke-width=".8"><rect x="1" y="1.5" width="8" height="5.5"/><path d="M3 9h4M5 7v2"/></svg>https://vornelquay.io/</li>
        <li><svg viewBox="0 0 10 10" fill="none" stroke="#222" stroke-width=".8"><rect x="1" y="2" width="8" height="6"/><path d="M1 2l4 3.5L9 2"/></svg>hello@vornelquay.io</li>
        <li><svg viewBox="0 0 10 10" fill="#222"><path d="M5 .5a3.2 3.2 0 0 0-3.2 3.2C1.8 6 5 9.5 5 9.5s3.2-3.5 3.2-5.8A3.2 3.2 0 0 0 5 .5zm0 4.4a1.2 1.2 0 1 1 0-2.4 1.2 1.2 0 0 1 0 2.4z"/></svg>1820 Harbor Row #410, Larkfield, Florida 33000</li>
        <li><svg viewBox="0 0 10 10" fill="#222"><path d="M2.3 1l1.6 2-1 1.1a6 6 0 0 0 3 3l1.1-1 2 1.6-1 1.3C4.5 9 1 5.5 1 2z"/></svg><span>555.014.2290</span></li>
      </ul>
    </div>
  </section>
  <section class="page toc">
    <div class="page-header"><span>VORNEL QUAY SECURITY</span><span>3</span></div>
    <div class="block">
      <h2 class="title">TABLE OF<br>CONTENTS</h2>
      <div class="rule"></div>
      <div class="toc-grid">
        <span>Lorem ipsum</span><span class="num">01</span><span>Lorem ipsum</span><span class="num">07</span>
        <span>Lorem ipsum</span><span class="num">02</span><span>Lorem ipsum</span><span class="num">08</span>
        <span>Lorem ipsum</span><span class="num">03</span><span>Lorem ipsum</span><span class="num">09</span>
        <span>Lorem ipsum</span><span class="num">04</span><span>Lorem ipsum</span><span class="num">10</span>
        <span>Lorem ipsum</span><span class="num">05</span><span>Lorem ipsum</span><span class="num">11</span>
        <span>Lorem ipsum</span><span class="num">06</span><span>Lorem ipsum</span><span class="num">12</span>
      </div>
    </div>
    <div class="photo photo-dark" role="img" aria-label="Red padlock on a circuit strip"></div>
  </section>
</div>

<!-- Spread: About / NAICS -->
<div class="spread" style="left:397px;top:326px">
  <section class="page grey about">
    <div class="page-header"><span>VORNEL QUAY SECURITY</span><span>4</span></div>
    <div class="block">
      <h2 class="title">ABOUT<br>COMPANY</h2>
      <div class="rule"></div>
      <div class="body-text">
        <p>Our analysts test networks, cloud platforms and applications to find weak points before attackers do, then explain every fix clearly. We pair practical security guidance with steady support, so teams of any size can protect data, systems and customers with confidence. Our analysts test networks, cloud platforms and applications to find weak points before attackers do, then explain every fix clearly.</p>
        <p>We pair practical security guidance with steady support, so teams of any size can protect data, systems and customers with confidence. Our analysts test networks, cloud platforms and applications to find weak points before attackers do, then explain every fix clearly.</p>
      </div>
    </div>
  </section>
  <section class="page naics">
    <div class="page-header"><span>VORNEL QUAY SECURITY</span><span>5</span></div>
    <div class="photo photo-chip" role="img" aria-label="Microchip on a dark red circuit board"></div>
    <div class="block">
      <h2 class="title">NAICS CODES</h2>
      <div class="rule"></div>
      <div class="naics-codes">
        <div class="naics-code"><b>541519</b><span>Other Computer Related Services</span></div>
        <div class="naics-code"><b>541512</b><span>Computer Systems Design Services</span></div>
        <div class="naics-code"><b>541690</b><span>Other Scientific and Technical Consulting Services</span></div>
        <div class="naics-code"><b>541511</b><span>Custom Computer Programming Services</span></div>
      </div>
    </div>
  </section>
</div>

<!-- Spread: CEO / History -->
<div class="spread" style="left:68px;top:617px">
  <section class="page grey ceo">
    <div class="page-header"><span>VORNEL QUAY SECURITY</span><span>6</span></div>
    <div class="block">
      <h2 class="title">CEO STATEMENT</h2>
      <div class="rule"></div>
      <div class="ceo-row">
        <div class="ceo-card">
          <div class="photo photo-dark" role="img" aria-label="CEO headshot"></div>
          <b>CEO Name</b>Vornel Quay Security CEO
        </div>
        <div class="body-text">
          <p>Our analysts test networks, cloud platforms and applications to find weak points before attackers do, then explain every fix clearly. We pair practical security guidance with steady support, so teams of any size can protect data, systems and customers with confidence.</p>
          <p>We pair practical security guidance with steady support, so teams of any size can protect data, systems and customers with confidence.</p>
        </div>
      </div>
    </div>
    <div class="photo photo-dark photo-band" role="img" aria-label="Red padlock on a dark background"></div>
  </section>
  <section class="page grey">
    <div class="page-header"><span>VORNEL QUAY SECURITY</span><span>7</span></div>
    <div class="history">
      <div class="photo photo-red" role="img" aria-label="Red padlocks over dark circuitry"></div>
      <div class="block">
        <h2 class="title">COMPANY<br>HISTORY</h2>
        <div class="body-text">
          <p>Our analysts test networks, cloud platforms and applications to find weak points before attackers do, then explain every fix clearly. We pair practical security guidance with steady support, so teams of any size can protect data, systems and customers with confidence. Our analysts test networks, cloud platforms and applications to find weak points before attackers do, then explain every fix clearly.</p>
          <p>We pair practical security guidance with steady support, so teams of any size can protect data, systems and customers with confidence. Our analysts test networks, cloud platforms and applications to find weak points before attackers do, then explain every fix clearly.</p>
        </div>
      </div>
    </div>
  </section>
</div>

<!-- Spread: Vision / Team -->
<div class="spread" style="left:397px;top:617px">
  <section class="page vision">
    <div class="page-header"><span>VORNEL QUAY SECURITY</span><span>8</span></div>
    <div class="block">
      <h2 class="title">VISION &amp; MISSON</h2>
      <div class="rule"></div>
      <div class="vm-row" style="margin-top:16px">
        <div class="vm-col">
          <div class="vm-head"><svg viewBox="0 0 7 6"><path d="M0 6C1 2 3 1.5 5 1.5V0l2 2.3-2 2.3V3C3 3 1.5 3.8 0 6z" fill="#a80402"/></svg>VISION</div>
          <p class="body-text">Our analysts test networks, cloud platforms and applications to find weak points before attackers do, then explain every fix clearly.</p>
        </div>
        <div class="photo photo-red" role="img" aria-label="Red circuit board close-up"></div>
      </div>
      <div class="vm-row">
        <div class="photo photo-red" role="img" aria-label="Red circuit board close-up"></div>
        <div class="vm-col">
          <div class="vm-head"><svg viewBox="0 0 7 6"><path d="M0 6C1 2 3 1.5 5 1.5V0l2 2.3-2 2.3V3C3 3 1.5 3.8 0 6z" fill="#a80402"/></svg>MISSON</div>
          <p class="body-text">We pair practical security guidance with steady support, so teams of any size can protect data, systems and customers with confidence.</p>
        </div>
      </div>
    </div>
  </section>
  <section class="page team">
    <div class="page-header"><span>VORNEL QUAY SECURITY</span><span>9</span></div>
    <div class="block">
      <h2 class="title">TEAM BIOS</h2>
      <div class="rule"></div>
      <div class="bio"><div class="photo photo-dark" role="img" aria-label="Team member photo"></div><div><p class="body-text">We pair practical security guidance with steady support, so teams of any size can protect data, systems and customers with confidence.</p><p class="bio-name">Team Member's Name, Position</p></div></div>
      <div class="bio"><div class="photo photo-dark" role="img" aria-label="Team member photo"></div><div><p class="body-text">We pair practical security guidance with steady support, so teams of any size can protect data, systems and customers with confidence.</p><p class="bio-name">Team Member's Name, Position</p></div></div>
      <div class="bio"><div class="photo photo-dark" role="img" aria-label="Team member photo"></div><div><p class="body-text">We pair practical security guidance with steady support, so teams of any size can protect data, systems and customers with confidence.</p><p class="bio-name">Team Member's Name, Position</p></div></div>
    </div>
    <div class="photo photo-dark photo-band" role="img" aria-label="Dark circuit band with red padlock"></div>
  </section>
</div>

<!-- Spread: Values / Services -->
<div class="spread" style="left:68px;top:908px">
  <section class="page values">
    <div class="page-header"><span>VORNEL QUAY SECURITY</span><span>10</span></div>
    <div class="photo photo-red" role="img" aria-label="Red padlocks on a circuit board"></div>
    <div class="block">
      <h2 class="title">OUR VALUES</h2>
      <div class="rule"></div>
      <p class="body-text">Our analysts test networks, cloud platforms and applications to find weak points before attackers do, then explain every fix clearly. We pair practical security guidance with steady support, so teams of any size can protect data, systems and customers with confidence.</p>
    </div>
  </section>
  <section class="page services">
    <div class="page-header"><span>VORNEL QUAY SECURITY</span><span>11</span></div>
    <div class="block">
      <h2 class="title">OUR SERVICES</h2>
      <div class="rule"></div>
      <div class="service"><div class="service-label">Penetration<br>Testing</div><p class="service-desc">Our analysts test networks, cloud platforms and applications to find weak points before attackers do, then explain every fix clearly.</p></div>
      <div class="service"><div class="service-label">Red<br>Team/Threat<br>Emulation</div><p class="service-desc">Our analysts test networks, cloud platforms and applications to find weak points before attackers do, then explain every fix clearly.</p></div>
      <div class="service"><div class="service-label">Cloud<br>Security<br>Assessments</div><p class="service-desc">Our analysts test networks, cloud platforms and applications to find weak points before attackers do, then explain every fix clearly.</p></div>
    </div>
  </section>
</div>

<!-- Spread: Pen Testing / Projects -->
<div class="spread" style="left:397px;top:908px">
  <section class="page grey pentest">
    <div class="page-header"><span>VORNEL QUAY SECURITY</span><span>12</span></div>
    <div class="block">
      <h2 class="title">PENETRATION TESTING</h2>
      <div class="rule"></div>
      <p class="stage">Reconnaissance</p>
      <p class="step"><b>Gathering Information About the Target</b>This stage maps targets and records findings for the next step.</p>
      <p class="step"><b>Creating a Profile of the Target</b>This stage maps targets and records findings for the next step.</p>
      <p class="stage">Scanning</p>
      <p class="step"><b>Identifying Open Ports and Services</b>This stage maps targets and records findings for the next step.</p>
      <p class="step"><b>Identifying Potential Vulnerabilities</b>This stage maps targets and records findings for the next step.</p>
      <p class="stage">Exploitation</p>
      <p class="step"><b>Attempting to Exploit Vulnerabilities</b>This stage maps targets and records findings for the next step.</p>
      <p class="step"><b>Evaluating the Potential Impact</b>This stage maps targets and records findings for the next step.</p>
      <p class="step"><b>Providing Recommendations for Improving Security</b>This stage maps targets and records findings for the next step.</p>
    </div>
    <div class="photo photo-dark photo-band" role="img" aria-label="Dark circuit band"></div>
  </section>
  <section class="page projects">
    <div class="page-header"><span>VORNEL QUAY SECURITY</span><span>13</span></div>
    <div class="block">
      <h2 class="title">PROJECTS</h2>
      <div class="rule"></div>
      <div class="body-text">
        <p>Our analysts test networks, cloud platforms and applications to find weak points before attackers do, then explain every fix clearly. We pair practical security guidance with steady support, so teams of any size can protect data, systems and customers with confidence. Our analysts test networks, cloud platforms and applications to find weak points before attackers do, then explain every fix clearly.</p>
        <p>We pair practical security guidance with steady support, so teams of any size can protect data, systems and customers with confidence. Our analysts test networks, cloud platforms and applications to find weak points before attackers do, then explain every fix clearly.</p>
      </div>
    </div>
    <div class="photo photo-red photo-band" role="img" aria-label="Red padlock on a glowing circuit board"></div>
  </section>
</div>

</body>
</html>
```